Birchpoint Studio Complementary Pass

I’d like a complimentary pass for any 30-minute Birchpoint Studio session. Choose one of the following options: Infrared Sauna with Red Light, Massage Chair Veltrafix Compression Therapy, or Paraffin Wax Hand Bath.

Please incorporate the logo and brand colors into your design. I’d like a square image that will be printed on square business cards (no rectangles).

Please refer to the logo and menu for more details.

Contact Information for Business Card

See discretion

```html
<!DOCTYPE html>
<html lang="en">
<head>
<meta charset="utf-8">
<title>Birchpoint Studio Complimentary Pass</title>
<link rel="stylesheet" href="https://fonts.googleapis.com/css2?family=Montserrat:wght@700;800&family=Open+Sans:wght@400;600&family=Great+Vibes&display=swap">
<style>
  :root {
    --purple: #47338f;
    --orange: #ee6a4a;
    --white: #ffffff;
    --stage: #232323;
  }
  * { box-sizing: border-box; margin: 0; padding: 0; }
  html, body { width: 1200px; height: 800px; overflow: hidden; }
  body {
    background: var(--stage);
    font-family: "Open Sans", Arial, sans-serif;
    display: flex; align-items: center; justify-content: center; gap: 80px;
  }
  .card {
    width: 440px; height: 440px; border-radius: 40px; overflow: hidden; position: relative;
  }
  .card-back {
    background: var(--purple); color: var(--white);
    display: flex; flex-direction: column; align-items: center; justify-content: center; gap: 6px;
  }
  .brand-name {
    font-family: "Montserrat", Arial, sans-serif; font-weight: 700; line-height: 1;
  }
  .card-back .brand-name { font-size: 64px; color: var(--white); }
  .card-back .brand-sub { font-family: "Montserrat", Arial, sans-serif; font-weight: 700; font-size: 17px; letter-spacing: 4px; color: var(--white); }

  .card-front { background: var(--white); color: var(--purple); text-align: center; padding-top: 30px; }
  .card-front .brand-name { font-size: 30px; color: var(--purple); }
  .card-front .brand-sub { font-family: "Montserrat", Arial, sans-serif; font-weight: 700; font-size: 8px; letter-spacing: 2px; color: var(--purple); margin-top: 3px; }

  .pass-title { display: flex; align-items: center; justify-content: center; gap: 12px; margin-top: 12px; }
  .pass-title .rule { width: 50px; height: 1.5px; background: var(--purple); }
  .script-heading { font-family: "Great Vibes", cursive; font-size: 40px; color: var(--purple); line-height: 1; }
  .pass-label { font-family: "Montserrat", Arial, sans-serif; font-weight: 800; font-size: 25px; color: var(--orange); margin-top: 4px; }
  .pass-offer { font-size: 14.5px; line-height: 1.35; margin-top: 4px; }
  .pass-offer .accent { color: var(--orange); }
  .pass-offer .choose { color: var(--orange); font-family: "Montserrat", Arial, sans-serif; font-weight: 800; }

  .options { display: grid; grid-template-columns: 1fr 1.45fr 1fr; margin-top: 12px; color: var(--white); font-size: 12.5px; line-height: 1.25; }
  .option { padding: 10px 6px; display: flex; align-items: center; justify-content: center; }
  .option-orange { background: var(--orange); }
  .option-purple { background: var(--purple); }

  .contact-name { font-family: "Montserrat", Arial, sans-serif; font-weight: 800; font-size: 22px; color: var(--orange); margin-top: 12px; line-height: 1.1; }
  .contact-role { font-weight: 600; font-size: 11px; }
  .contact-grid { display: flex; justify-content: space-between; padding: 0 30px; font-size: 10px; margin-top: 8px; }
  .contact-item { display: flex; align-items: center; gap: 4px; }
  .contact-item svg { width: 10px; height: 10px; fill: var(--orange); }
  .contact-rule { height: 1px; background: var(--purple); margin: 6px 30px; }
  .contact-address { display: flex; justify-content: center; }
  .footnote { color: var(--orange); font-size: 9.5px; margin-top: 6px; }
</style>
</head>
<body>
  <section class="card card-back">
    <div class="brand-name">Solvera</div>
    <div class="brand-sub">PHYSICAL THERAPY</div>
  </section>

  <section class="card card-front">
    <div class="brand-name">Solvera</div>
    <div class="brand-sub">PHYSICAL THERAPY</div>

    <div class="pass-title">
      <span class="rule"></span>
      <h1 class="script-heading">Birchpoint Studio</h1>
      <span class="rule"></span>
    </div>
    <h2 class="pass-label">COMPLIMENTARY PASS</h2>
    <p class="pass-offer">Any <span class="accent">30-Minute</span> Birchpoint Studio Session.<br>on us! <span class="choose">Choose one:</span></p>

    <div class="options">
      <div class="option option-orange">Infrared Sauna<br>+ Red Light</div>
      <div class="option option-purple">Massage Chair Veltrafix<br>Compression Therapy</div>
      <div class="option option-orange">Paraffin Wax<br>Hand Bath</div>
    </div>

    <p class="contact-name">Marta Lindqvist</p>
    <p class="contact-role">Managing Director</p>

    <div class="contact-grid">
      <span class="contact-item"><svg viewBox="0 0 10 10"><path d="M2 0.5 L3.8 2.6 L2.8 3.6 Q3.8 5.8 6.2 7 L7.2 6 L9.5 7.8 L8.2 9.5 Q2.5 8.8 0.5 1.8 Z"/></svg>+555-210-4486</span>
      <span class="contact-item"><svg viewBox="0 0 10 10"><path d="M0.5 2 H9.5 V8.5 H0.5 Z M0.5 2 L5 5.5 L9.5 2" fill="none" stroke="#ee6a4a" stroke-width="1"/></svg>info@solverapt.com</span>
      <span class="contact-item"><svg viewBox="0 0 10 10"><circle cx="5" cy="5" r="4.2" fill="none" stroke="#ee6a4a" stroke-width="1.2"/><path d="M0.8 5 H9.2 M5 0.8 Q2.5 5 5 9.2 Q7.5 5 5 0.8" fill="none" stroke="#ee6a4a" stroke-width="0.8"/></svg>www.solverapt.com</span>
    </div>
    <div class="contact-rule"></div>
    <div class="contact-address">
      <span class="contact-item"><svg viewBox="0 0 10 10"><path d="M5 0.5 A3.2 3.2 0 0 1 8.2 3.7 Q8.2 6 5 9.5 Q1.8 6 1.8 3.7 A3.2 3.2 0 0 1 5 0.5 Z M5 2.5 A1.2 1.2 0 1 0 5 4.9 A1.2 1.2 0 1 0 5 2.5 Z"/></svg>Street, Apartment, City, State, Post Code, Country</span>
    </div>
    <p class="footnote">*For safety, a rest/cool-down period is required after 30 minutes in the sauna.</p>
  </section>
</body>
</html>
```